Wedding Videography Wordpress Website Theme

We need a modern and high-end website look for our wedding video and film business. We film weddings all over the United Kingdom and at European destinations so need something to reflect our work. The website should be visually stunning with images and videos being the focal point as this is what our services are.

The current website is www.brunolessway.com so you will be able to see our brand.

My Instagram is www.instagram.com/brunolesswayfilms so a new design should link in with this idea.

We need the following pages designed by the winning designer

1 - Homepage
2 - Films Index Page
3 - Testimonials
4 - Prices
5 - Reviews
6 - Meet Bruno (About)
7 - Contact
8 - Blog Index
9 - Blog Page

All pages must be consistent so have a similar style.

Pages on menu:
Meet Bruno
Videos
Packages
Testimionials
Journal (Blog)
Contact

We require a responsive look too. Over 90% of our visitors access the website via their mobile devices.

```html
<!DOCTYPE html>
<html lang="en">
<head>
<meta charset="utf-8">
<title>Reviews – Bruno Lessway Wedding Films</title>
<link href="https://fonts.googleapis.com/css2?family=Cormorant+Garamond:wght@500;600&family=Jost:wght@300;400;500&display=swap" rel="stylesheet">
<style>
:root{
  --gold:#a88a45;
  --gold-soft:#c8b27a;
  --star:#e8b830;
  --band:#e3d5ae;
  --band-soft:#f1e9d6;
  --ink:#2a2a2a;
  --muted:#6f6f6f;
  --faint:#b5b5b5;
  --page:#f3f3f3;
  --white:#ffffff;
}
*{margin:0;padding:0;box-sizing:border-box}
html,body{width:1200px;height:2506px;overflow:hidden;background:var(--page)}
body{position:relative;font-family:'Jost',sans-serif;color:var(--ink)}
.abs{position:absolute}
.serif{font-family:'Cormorant Garamond',serif}
.board-label{left:95px;top:88px;width:70px;height:205px;background:#e6e6e6;border-radius:6px}
.frame{background:var(--white);overflow:hidden}
.desktop{left:221px;top:0;width:688px;height:2506px}
.mobile{left:950px;top:0;width:174px;height:2506px}
.photo{position:absolute}
.play{position:absolute;width:30px;height:30px;border-radius:50%;background:rgba(255,255,255,.85);transform:translate(-50%,-50%)}
.play::after{content:"";position:absolute;left:12px;top:9px;border-left:9px solid #777;border-top:6px solid transparent;border-bottom:6px solid transparent}
.play.sm{width:22px;height:22px}
.play.sm::after{left:9px;top:6px;border-left:7px solid #777;border-top:5px solid transparent;border-bottom:5px solid transparent}
.hero-title{font-family:'Cormorant Garamond',serif;color:var(--gold-soft);letter-spacing:1px;text-align:center;width:100%}
.hero-sub{color:#fff;text-align:center;width:100%}
.nav a{position:absolute;top:47px;font-size:7px;color:#fff;text-decoration:none;letter-spacing:.3px;font-weight:500}
.brand{color:#fff;font-family:'Jost',sans-serif;font-weight:500;letter-spacing:2px}
.enquire{left:538px;top:39px;width:82px;height:24px;background:var(--band);font-size:7px;font-weight:500;display:flex;align-items:center;justify-content:center}
.section-title{font-family:'Cormorant Garamond',serif;color:var(--gold);text-align:center;width:100%;letter-spacing:1px;font-weight:500}
.avatar{position:absolute;border-radius:50%;border:2px solid var(--gold-soft);background:linear-gradient(135deg,#6d5a45,#c9b79a)}
.name{position:absolute;font-family:'Cormorant Garamond',serif;font-weight:600;letter-spacing:.5px;color:var(--ink)}
.venue{position:absolute;color:var(--faint)}
.quote{position:absolute;text-align:center;color:var(--muted);font-weight:300}
.stars{position:absolute;text-align:center;color:var(--star);letter-spacing:3px}
.married{position:absolute;text-align:center;font-family:'Cormorant Garamond',serif;font-weight:600;color:var(--ink)}
.d .name{font-size:10.5px}
.d .venue{font-size:6px}
.d .quote{left:407px;width:204px;font-size:7.3px;line-height:15px}
.d .stars{left:407px;width:204px;font-size:13px}
.d .married{left:407px;width:204px;font-size:7.5px}
.m .name{font-size:9px}
.m .venue{font-size:5.5px}
.m .quote{left:13px;width:148px;font-size:6.2px;line-height:14.3px}
.m .stars{left:13px;width:148px;font-size:12px}
.m .married{left:13px;width:148px;font-size:6.5px}
.btn-gold{position:absolute;background:var(--band);font-size:6.5px;font-weight:500;display:flex;align-items:center;justify-content:center;letter-spacing:.2px}
.btn-white{position:absolute;background:#fff;font-size:8px;display:flex;align-items:center;justify-content:center}
.insta-title{position:absolute;width:100%;text-align:center;font-family:'Cormorant Garamond',serif;color:#8a7a55;letter-spacing:4px}
.thumb{position:absolute}
.foot-brand{position:absolute;color:var(--gold-soft);font-weight:500;letter-spacing:2px;text-align:center}
.social{position:absolute;width:14px;height:14px;border:1px solid var(--gold-soft);border-radius:3px}
.foot-head{position:absolute;font-size:9.5px;font-weight:500;color:#444}
.foot-head::after{content:"";display:inline-block;width:13px;height:1px;background:#999;margin-left:6px;vertical-align:middle}
.foot-item{position:absolute;font-size:7px;color:#555}
.copy{position:absolute;font-size:5.5px;color:#aaa}
</style>
</head>
<body>

<div class="abs board-label" role="img" aria-label="Hand-lettered page label reading Reviews"></div>

<!-- Desktop page -->
<main class="abs frame desktop d">
  <div class="photo" style="left:0;top:0;width:688px;height:355px;background:linear-gradient(120deg,#3a2e26 0%,#5a4738 45%,#8c8a88 75%,#4a3d33 100%)" role="img" aria-label="Groom and bride walking hand in hand at a wedding ceremony"></div>
  <div class="abs" style="left:0;top:0;width:688px;height:355px;background:rgba(20,15,10,.35)"></div>
  <div class="abs brand" style="left:66px;top:48px;font-size:10px">BRUNO LESSWAY</div>
  <nav class="nav">
    <a style="left:227px">MEET BRUNO</a>
    <a style="left:292px">VIDEOS</a>
    <a style="left:342px">PACKAGES</a>
    <a style="left:406px">TESTIMONIALS</a>
    <a style="left:479px">JOURNAL</a>
  </nav>
  <div class="abs" style="left:406px;top:59px;width:12px;height:1px;background:var(--gold-soft)"></div>
  <div class="abs enquire">ENQUIRE</div>
  <h1 class="abs hero-title" style="top:170px;font-size:21px;font-weight:500">REVIEWS FORM COUPLES</h1>
  <p class="abs hero-sub" style="top:204px;font-size:8.5px">Reviews From Real Couples</p>

  <h2 class="abs section-title" style="top:379px;font-size:17px">WEDDING VIDEO REVIEWS</h2>

  <!-- Review 1 -->
  <div class="photo" style="left:0;top:431px;width:377px;height:274px;background:linear-gradient(110deg,#a89684,#c98a55 55%,#6f7f52 80%,#5e6d80)" role="img" aria-label="Bride with flower crown beside a floral arch at a Greek island ceremony"></div>
  <div class="play" style="left:188px;top:568px"></div>
  <div class="avatar" style="left:424px;top:473px;width:43px;height:43px"></div>
  <div class="name" style="left:474px;top:481px">ROSIE + DANIEL</div>
  <div class="venue" style="left:476px;top:499px">Thorne Hall, Yorkshire</div>
  <p class="quote" style="top:537px">“We were blown away by the quality of Bruno's work. When we met Bruno he was friendly and it was as though we had known him for years. He was incredible and he encouraged us to spend moments on our own to enjoy the day. We are truly grateful for all the work Bruno has done and we cannot thank him enough.”</p>
  <div class="stars" style="top:632px">★★★★★</div>
  <div class="married" style="top:661px">Married on Ios Island, Greece</div>

  <!-- Review 2 -->
  <div class="photo" style="left:0;top:739px;width:377px;height:275px;background:linear-gradient(110deg,#7a5a48,#d8c3ad 40%,#8a6650 65%,#3d4356)" role="img" aria-label="Laughing bride holding a bouquet next to the groom"></div>
  <div class="play" style="left:188px;top:876px"></div>
  <div class="avatar" style="left:424px;top:781px;width:43px;height:43px"></div>
  <div class="name" style="left:476px;top:789px">MEGAN + TOM</div>
  <div class="venue" style="left:476px;top:807px">North Oaks Inn</div>
  <p class="quote" style="top:842px">Absolutely amazing videographer! What can we say, our short film captures our day perfectly and includes everything we wanted. Both Bruno and Simon were most professional and easy to work with on the day. They captured moments that I wouldn't have seen otherwise (like groom panicking beforehand). Would highly recommend!</p>
  <div class="stars" style="top:940px">★★★★★</div>
  <div class="married" style="top:969px">Married on Ios Island, Greece</div>

  <!-- Review 3 -->
  <div class="photo" style="left:0;top:1046px;width:377px;height:274px;background:linear-gradient(110deg,#141624,#6b5348 40%,#c9b3a3 55%,#1f2030)" role="img" aria-label="Bride and groom smiling at night among sparklers"></div>
  <div class="play" style="left:188px;top:1183px"></div>
  <div class="avatar" style="left:424px;top:1088px;width:43px;height:43px"></div>
  <div class="name" style="left:476px;top:1096px">HANNAH + LUKE</div>
  <div class="venue" style="left:476px;top:1114px">North Oaks Inn</div>
  <p class="quote" style="top:1148px">Bruno was our videographer for our wedding in July. We couldn't fault the video he made for us everyone commented on just how amazing it was, captured our day perfectly. The best thing we got from the day. Thanks so much Bruno</p>
  <div class="stars" style="top:1230px">★★★★★</div>

  <!-- Review 4 -->
  <div class="photo" style="left:0;top:1357px;width:377px;height:275px;background:linear-gradient(110deg,#5a3a2a,#b98a6c 40%,#2f3b2c 70%,#c8a086)" role="img" aria-label="Close-up of the couple about to kiss with a white flower"></div>
  <div class="play" style="left:188px;top:1494px"></div>
  <div class="avatar" style="left:424px;top:1372px;width:43px;height:43px"></div>
  <div class="name" style="left:476px;top:1381px">SOPHIE + MARK</div>
  <div class="venue" style="left:476px;top:1399px">North Oaks Inn</div>
  <p class="quote" style="top:1430px">“Definitely recommend going for Bruno. He captured the love and connection we wanted but in a natural way. It was just the beautiful video I could have only dreamed of. It was more than I imagined. In the beginning, I wasn't that fussed about booking a videographer and you go ‘I have a photographer and that is enough’. There are things on there that I will always be able to look back on, like my dad's speech, our little children running around, my husband's speech and our first dance. As time goes on your memory fades but I will have this video forever ”</p>
  <div class="stars" style="top:1592px">★★★★★</div>

  <!-- Review 5 -->
  <div class="photo" style="left:0;top:1675px;width:377px;height:275px;background:linear-gradient(110deg,#6e5a45,#9a8266 50%,#5d4b3a)" role="img" aria-label="Two grooms embracing in a golden wheat field"></div>
  <div class="play" style="left:188px;top:1812px"></div>
  <div class="avatar" style="left:424px;top:1738px;width:43px;height:43px"></div>
  <div class="name" style="left:474px;top:1746px">JAMIE AND OLIVER</div>
  <div class="venue" style="left:476px;top:1764px">North Oaks Inn</div>
  <p class="quote" style="top:1796px">Bruno thank you!!! We have just watched it and all in bits!!! You caught the most amazing parts of our day!!! We can't thank you enough!</p>
  <div class="stars" style="top:1853px">★★★★★</div>

  <div class="btn-gold" style="left:283px;top:2000px;width:121px;height:24px">LOAD MORE TESTIMONIALS</div>

  <!-- Instagram band -->
  <section class="abs" style="left:0;top:2055px;width:688px;height:269px;background:var(--band)">
    <h2 class="insta-title" style="top:42px;font-size:17px;font-weight:500">FOLLOW ME ON INSTAGRAM</h2>
    <div class="thumb" style="left:65px;top:83px;width:83px;height:92px;background:linear-gradient(135deg,#8a7a66,#cfc7bb)" role="img" aria-label="Couple on a village street"></div>
    <div class="thumb" style="left:159px;top:83px;width:83px;height:92px;background:linear-gradient(135deg,#3b4560,#d9d2c8)" role="img" aria-label="Groom and bride laughing"></div>
    <div class="thumb" style="left:255px;top:83px;width:83px;height:92px;background:linear-gradient(180deg,#c9d2d6,#9e9a70)" role="img" aria-label="Horse-drawn carriage in a field"></div>
    <div class="thumb" style="left:349px;top:83px;width:83px;height:92px;background:linear-gradient(135deg,#2a2a2a,#cfc3b3)" role="img" aria-label="Father and bride arriving"></div>
    <div class="thumb" style="left:444px;top:83px;width:83px;height:92px;background:linear-gradient(135deg,#2d2f33,#caa58c)" role="img" aria-label="Couple exchanging vows"></div>
    <div class="thumb" style="left:538px;top:83px;width:83px;height:92px;background:linear-gradient(180deg,#7ea0c8,#b6c2a0)" role="img" aria-label="Couple jumping outdoors"></div>
    <div class="btn-white" style="left:269px;top:205px;width:148px;height:31px">Follow me @brunolesswayfilms</div>
  </section>

  <!-- Footer -->
  <div class="foot-brand" style="left:56px;top:2381px;width:120px;font-size:9px">BRUNO LESSWAY</div>
  <div class="social" style="left:88px;top:2429px"></div>
  <div class="social" style="left:110px;top:2429px"></div>
  <div class="social" style="left:132px;top:2429px;border-radius:50%"></div>
  <div class="foot-head" style="left:236px;top:2368px">Contact</div>
  <svg class="abs" style="left:236px;top:2398px" width="10" height="10" viewBox="0 0 24 24" fill="none" stroke="#999" stroke-width="2"><path d="M5 3h4l2 5-3 2a11 11 0 0 0 6 6l2-3 5 2v4a2 2 0 0 1-2 2A17 17 0 0 1 3 5a2 2 0 0 1 2-2z"/></svg>
  <div class="foot-item" style="left:258px;top:2398px">07700 900 123</div>
  <svg class="abs" style="left:236px;top:2426px" width="10" height="10" viewBox="0 0 24 24" fill="none" stroke="#999" stroke-width="2"><rect x="3" y="5" width="18" height="14"/><path d="M3 6l9 7 9-7"/></svg>
  <div class="foot-item" style="left:258px;top:2426px">films@brunolessway.com</div>
  <div class="foot-head" style="left:401px;top:2368px">Links</div>
  <div class="foot-item" style="left:403px;top:2393px">FAQ's</div>
  <div class="foot-item" style="left:403px;top:2413px">Wedding Photography</div>
  <div class="foot-item" style="left:403px;top:2432px">Commercial</div>
  <div class="foot-item" style="left:526px;top:2393px">North East Wedding Venues</div>
  <div class="foot-item" style="left:526px;top:2413px">Free Speeches Guide</div>
  <div class="foot-item" style="left:526px;top:2432px">Blog</div>
  <div class="copy" style="left:0;width:688px;text-align:center;top:2472px">© Copyright 2022 Bruno Lessway Films Ltd All Rights Reserved</div>
</main>

<!-- Mobile page -->
<main class="abs frame mobile m">
  <div class="photo" style="left:0;top:0;width:174px;height:270px;background:linear-gradient(150deg,#3a2e26,#5a4738 50%,#7a6a5c)" role="img" aria-label="Groom leading the bride by the hand"></div>
  <div class="abs" style="left:0;top:0;width:174px;height:270px;background:rgba(20,15,10,.35)"></div>
  <div class="abs brand" style="left:8px;top:35px;font-size:6.5px;letter-spacing:1.2px">BRUNO LESSWAY</div>
  <svg class="abs" style="left:152px;top:28px" width="13" height="10" viewBox="0 0 13 10" stroke="#fff" stroke-width="1.4"><path d="M0 1h13M2 5h11M4 9h9"/></svg>
  <h1 class="abs hero-title" style="top:106px;font-size:19px;line-height:25px;font-weight:500">REVIEWS<br>FROM COUPLES</h1>
  <p class="abs hero-sub" style="top:160px;font-size:6.5px">REVIEWS FROM REAL COUPLES</p>

  <h2 class="abs section-title" style="top:282px;font-size:15px;line-height:17px">WEDDING<br>VIDEO REVIEWS</h2>

  <div class="photo" style="left:0;top:332px;width:174px;height:176px;background:linear-gradient(110deg,#a89684,#c98a55 55%,#6f7f52)" role="img" aria-label="Bride beside a floral arch"></div>
  <div class="play sm" style="left:87px;top:413px"></div>
  <div class="avatar" style="left:13px;top:522px;width:42px;height:42px"></div>
  <div class="name" style="left:62px;top:531px">ROSIE + DANIEL</div>
  <div class="venue" style="left:63px;top:546px">Thorne Hall, Yorkshire</div>
  <p class="quote" style="top:578px">“We were blown away by the quality of Bruno's work. When we met Bruno he was friendly and it was as though we had known him for years. He was incredible and he encouraged us to spend moments on our own to enjoy the day. We are truly grateful for all the work Bruno has done and we cannot thank him enough.”</p>
  <div class="stars" style="top:697px">★★★★★</div>
  <div class="married" style="top:722px">Married on Ios Island, Greece</div>

  <div class="photo" style="left:0;top:750px;width:174px;height:225px;background:linear-gradient(110deg,#7a5a48,#d8c3ad 45%,#3d4356)" role="img" aria-label="Laughing bride next to the groom"></div>
  <div class="play sm" style="left:87px;top:868px"></div>
  <div class="avatar" style="left:18px;top:994px;width:42px;height:42px"></div>
  <div class="name" style="left:68px;top:1003px">MEGAN + TOM</div>
  <div class="venue" style="left:68px;top:1018px">North Oaks Inn</div>
  <p class="quote" style="top:1047px">Absolutely amazing videographer! What can we say, our short film captures our day perfectly and includes everything we wanted. Both Bruno and Simon were most professional and easy to work with on the day. They captured moments that I wouldn't have seen otherwise (like groom panicking beforehand). Would highly recommend!</p>
  <div class="stars" style="top:1174px">★★★★★</div>

  <div class="photo" style="left:0;top:1219px;width:174px;height:177px;background:linear-gradient(110deg,#a89684,#c98a55 55%,#6f7f52)" role="img" aria-label="Bride beside a floral arch"></div>
  <div class="play sm" style="left:87px;top:1301px"></div>
  <div class="avatar" style="left:13px;top:1410px;width:42px;height:42px"></div>
  <div class="name" style="left:62px;top:1419px">ROSIE + DANIEL</div>
  <div class="venue" style="left:63px;top:1434px">Thorne Hall, Yorkshire</div>
  <p class="quote" style="top:1466px">“We were blown away by the quality of Bruno's work. When we met Bruno he was friendly and it was as though we had known him for years. He was incredible and he encouraged us to spend moments on our own to enjoy the day. We are truly grateful for all the work Bruno has done and we cannot thank him enough.”</p>
  <div class="stars" style="top:1585px">★★★★★</div>
  <div class="married" style="top:1609px">Married on Ios Island, Greece</div>
  <div class="btn-gold" style="left:30px;top:1640px;width:115px;height:25px;font-size:6px">LOAD MORE TESTIMONIALS</div>

  <section class="abs" style="left:0;top:1683px;width:174px;height:399px;background:var(--band-soft)">
    <h2 class="insta-title" style="top:26px;font-size:12.5px;line-height:19px;letter-spacing:3px;font-weight:500">FOLLOW ME ON<br>INSTAGRAM</h2>
    <div class="thumb" style="left:4px;top:78px;width:80px;height:83px;background:linear-gradient(135deg,#3b4560,#d9d2c8)" role="img" aria-label="Groom and bride laughing"></div>
    <div class="thumb" style="left:88px;top:78px;width:79px;height:83px;background:linear-gradient(135deg,#8a7a66,#cfc7bb)" role="img" aria-label="Couple on a village street"></div>
    <div class="thumb" style="left:4px;top:165px;width:80px;height:83px;background:linear-gradient(180deg,#dfe4e6,#9e9a70)" role="img" aria-label="Horse-drawn carriage in a field"></div>
    <div class="thumb" style="left:88px;top:165px;width:79px;height:83px;background:linear-gradient(135deg,#2a2a2a,#cfc3b3)" role="img" aria-label="Father and bride arriving"></div>
    <div class="thumb" style="left:4px;top:252px;width:80px;height:83px;background:linear-gradient(135deg,#2d2f33,#caa58c)" role="img" aria-label="Couple exchanging vows"></div>
    <div class="thumb" style="left:88px;top:252px;width:79px;height:83px;background:linear-gradient(180deg,#7ea0c8,#b6c2a0)" role="img" aria-label="Couple jumping outdoors"></div>
    <div class="btn-white" style="left:20px;top:352px;width:139px;height:28px;font-size:7px">Follow me @brunolesswayfilms</div>
  </section>

  <div class="foot-brand" style="left:0;top:2135px;width:174px;font-size:8.5px">BRUNO LESSWAY</div>
  <div class="social" style="left:60px;top:2166px"></div>
  <div class="social" style="left:80px;top:2166px"></div>
  <div class="social" style="left:100px;top:2166px;border-radius:50%"></div>
  <div class="foot-head" style="left:22px;top:2213px">Contact</div>
  <svg class="abs" style="left:22px;top:2241px" width="9" height="9" viewBox="0 0 24 24" fill="none" stroke="#999" stroke-width="2"><path d="M5 3h4l2 5-3 2a11 11 0 0 0 6 6l2-3 5 2v4a2 2 0 0 1-2 2A17 17 0 0 1 3 5a2 2 0 0 1 2-2z"/></svg>
  <div class="foot-item" style="left:43px;top:2241px;font-size:6.5px">07700 900 123</div>
  <svg class="abs" style="left:22px;top:2267px" width="9" height="9" viewBox="0 0 24 24" fill="none" stroke="#999" stroke-width="2"><rect x="3" y="5" width="18" height="14"/><path d="M3 6l9 7 9-7"/></svg>
  <div class="foot-item" style="left:43px;top:2267px;font-size:6.5px">films@brunolessway.com</div>
  <div class="foot-head" style="left:22px;top:2297px">Links</div>
  <div class="foot-item" style="left:24px;top:2320px;font-size:6.5px">FAQ's</div>
  <div class="foot-item" style="left:24px;top:2339px;font-size:6.5px">Wedding Photography</div>
  <div class="foot-item" style="left:24px;top:2358px;font-size:6.5px">Commercial</div>
  <div class="foot-item" style="left:24px;top:2378px;font-size:6.5px">North East Wedding Venues</div>
  <div class="foot-item" style="left:24px;top:2397px;font-size:6.5px">Free Speeches Guide</div>
  <div class="foot-item" style="left:24px;top:2416px;font-size:6.5px">Blog</div>
  <div class="copy" style="left:24px;top:2445px">© Copyright 2022 Bruno Lessway Films Ltd</div>
  <div class="copy" style="left:24px;top:2458px">All Rights Reserved</div>
</main>

</body>
</html>
```